Consulting firm need a professional powerpoint design

A startup Climate change firm needs a powerpoint template design. The design should reflect aspects of climate change adaptation, resilience and environmental sustainability.

The powerpoint design must convey aspects of nature and climate action for a resilient society.

The last slide of the powerpoint must have a allocation for a slogan such as 'Linking science and decision-making'.

Use the colors in the logo and business card for the powerpoint design.

Target Market(s)

Government and industry

Font styles to use
Sans Serif
Other font styles liked:
• nexa font family

Colors
85cae6
abd037
fece3e

Requirements
Must have
• - Colors used in logo and business card
- Convey science and nature
- Professional
Nice to have
• Many pages
Should not have
• Not complicated

```html
<!DOCTYPE html>
<html lang="en">
<head>
<meta charset="utf-8">
<title>Important Slides</title>
<link rel="stylesheet" href="https://fonts.googleapis.com/css2?family=Jost:wght@300&family=Roboto:ital,wght@0,400;0,500;0,700;1,400&display=swap">
<style>
  :root {
    --sky: #85cae6;
    --leaf: #abd037;
    --sun: #fece3e;
    --ink: #2b2d3a;
    --navy: #3a3f5c;
    --deep-blue: #1f7fb4;
    --deep-green: #2f9a3e;
    --orange: #f08a24;
    --haze: #e6f3f9;
    --leaf-tint: #eef4dc;
    --turbine: #cfe8f3;
    --white: #ffffff;
  }
  * { box-sizing: border-box; margin: 0; padding: 0; }
  html, body { width: 1200px; height: 240px; overflow: hidden; background: var(--white); }
  body { position: relative; font-family: "Roboto", Arial, sans-serif; color: var(--ink); }

  .backdrop { position: absolute; inset: 0; }

  .page-title {
    position: absolute; left: 20px; top: 17px;
    font-family: "Jost", sans-serif; font-weight: 300;
    font-size: 27px; letter-spacing: 22.6px; color: #111; white-space: nowrap;
  }

  .slide {
    position: absolute; top: 55px; width: 267px; height: 150px;
    background: var(--white); border: 0.5px solid #d8ecf2;
    box-shadow: 3px 4px 7px rgba(0,0,0,0.12); overflow: hidden;
  }
  .slide--quote { left: 15px; }
  .slide--split { left: 316px; }
  .slide--feature { left: 617px; }
  .slide--charts { left: 918px; }

  .accent-rule {
    position: absolute; left: 0; right: 0; bottom: 0; height: 1.6px;
    background: linear-gradient(90deg, var(--orange) 0%, var(--sun) 33%, var(--deep-blue) 34%, var(--sky) 66%, var(--deep-green) 67%, var(--leaf) 100%);
  }

  /* Quote slide */
  .leaf-art {
    position: absolute; right: 0; top: 0; width: 72px; height: 90px;
    background: radial-gradient(ellipse at 60% 40%, var(--leaf-tint) 0%, rgba(238,244,220,0.4) 60%, rgba(255,255,255,0) 100%);
  }
  .quote-mark {
    position: absolute; font-family: Georgia, serif; font-weight: 700; line-height: 1;
  }
  .slide--quote .quote-mark { left: 19px; top: 28px; font-size: 48px; color: var(--leaf); }
  .quote-text {
    position: absolute; left: 50px; top: 50px; width: 170px;
    font-style: italic; font-size: 7.6px; line-height: 9.8px; color: var(--ink);
  }

  /* Split slide */
  .split-panel { position: absolute; left: 133px; top: 0; right: 0; bottom: 0; background: var(--sun); }
  .slide-heading {
    position: absolute; left: 13px; top: 11px;
    font-size: 8.6px; font-weight: 500; color: var(--navy);
  }
  .body-copy { position: absolute; font-size: 4.1px; line-height: 5.9px; color: var(--ink); }
  .slide--split .body-copy { left: 13px; top: 37px; width: 112px; }
  .slide--split .quote-mark { left: 139px; top: 18px; font-size: 46px; color: var(--navy); }
  .slide--split .quote-text { left: 168px; top: 37px; width: 88px; font-size: 6.8px; line-height: 8.8px; color: var(--navy); }

  /* Feature slide */
  .feature-blob { position: absolute; left: 0; top: 0; }
  .feature-heading {
    position: absolute; left: 25px; top: 40px;
    font-size: 11.3px; font-weight: 500; line-height: 14.6px; color: var(--white);
  }
  .slide--feature .body-copy { left: 120px; top: 20px; width: 100px; }
  .turbine-art {
    position: absolute; right: 4px; top: 6px; width: 62px; height: 142px;
    background: linear-gradient(180deg, rgba(207,232,243,0.2) 0%, var(--turbine) 55%, rgba(207,232,243,0.7) 100%);
  }

  /* Charts slide */
  .slide--charts .slide-heading { top: 10px; }
  .subheading { position: absolute; left: 13px; top: 24px; font-size: 4.2px; }
  .title-rule {
    position: absolute; left: 13px; top: 31px; width: 241px; height: 1px;
    background: linear-gradient(90deg, var(--orange) 0%, var(--sun) 33%, var(--deep-blue) 34%, var(--sky) 66%, var(--deep-green) 67%, var(--leaf) 100%);
  }
  .chart-title { position: absolute; top: 37px; font-size: 4.2px; font-weight: 700; }
  .chart-title--pies { left: 13px; }
  .chart-title--bars { left: 136px; }
  .charts { position: absolute; left: 0; top: 0; }
  .chart-label { font-family: "Roboto", Arial, sans-serif; font-size: 3.6px; fill: var(--ink); }
  .legend-label { font-family: "Roboto", Arial, sans-serif; font-size: 1.8px; fill: var(--ink); }
  .page-badge {
    position: absolute; left: 242px; top: 137px; width: 12px; height: 11px;
    background: var(--leaf); border-radius: 2px 2px 0 0;
    font-size: 3.6px; font-weight: 700; color: var(--white);
    display: flex; align-items: center; justify-content: center;
  }
</style>
</head>
<body>
  <svg class="backdrop" width="1200" height="240" viewBox="0 0 1200 240" aria-hidden="true">
    <polygon points="70,240 345,240 1000,0 722,0" fill="var(--haze)"/>
  </svg>

  <h1 class="page-title">IMPORTANT SLIDES</h1>

  <section class="slide slide--quote">
    <div class="leaf-art" role="img" aria-label="Faint line illustration of leaves"></div>
    <span class="quote-mark">&ldquo;</span>
    <p class="quote-text">Perspiciatis unde omnis iste natus error sit voluptatem accusantium doloremque, totam rem aperiam, eaque ipsa quae ab illo inventore veritatis et quasi architecto beatae vitae dicta sunt explicabo. Nemo enim ipsam voluptatem quia voluptas sit aspernatur aut odit aut fugit, sed quia consequuntur magni.</p>
    <div class="accent-rule"></div>
  </section>

  <section class="slide slide--split">
    <div class="split-panel"></div>
    <h2 class="slide-heading">Please add slide title here</h2>
    <p class="body-copy">ut labore et dolore magnam aliquam quaerat voluptatem. Ut enim ad minima veniam, quis nostrum exercitationem ullam corporiut labore et dolore magnam aliquam quaerat voluptatem. Ut enim ad minima veniam, quis nostrum exercitationem ullam corporis suscipit laboriosam, nisi ut aliquid ex ea commodi consequatur s suscipit laboriosam, nisi ut aliquid ex ea commodi consequatur?</p>
    <span class="quote-mark">&ldquo;</span>
    <p class="quote-text">ut labore et dolore magnam aliquam quaerat voluptatem. Ut enim ad minima veniam, quis nostrum exercitationem ullam corporis suscipit laboriosam, nisi ut aliquid ex ea commodi consequatur?</p>
  </section>

  <section class="slide slide--feature">
    <div class="turbine-art" role="img" aria-label="Light blue illustration of wind turbines"></div>
    <svg class="feature-blob" width="267" height="150" viewBox="0 0 267 150" aria-hidden="true">
      <path d="M14,36 C24,14 62,14 82,26 C96,35 96,52 100,66 C104,80 124,88 131,108 C136,128 118,138 100,135 C84,132 76,120 64,112 C52,104 30,106 18,92 C6,78 6,52 14,36 Z" fill="var(--sky)"/>
    </svg>
    <h2 class="feature-heading">Important<br>heading<br>please</h2>
    <p class="body-copy">Sed ut perspiciatis unde omnis iste natus error sit voluptatem accusantium doloremque laudantium, totam rem aperiam, eaque ipsa quae ab illo inventore veritatis et quasi architecto beatae vitae dicta sunt explicabo. Nemo enim ipsam voluptatem quia voluptas sit aspernatur aut odit aut fugit, sed quia consequuntur magni dolores eos qui ratione voluptatem sequi nesciunt. Neque porro quisquam est.</p>
    <div class="accent-rule"></div>
  </section>

  <section class="slide slide--charts">
    <h2 class="slide-heading">Topic of the slide</h2>
    <p class="subheading">Any sub title here please</p>
    <div class="title-rule"></div>
    <p class="chart-title chart-title--pies">Your Chart title Here Please</p>
    <p class="chart-title chart-title--bars">Your Chart title Here Please</p>
    <svg class="charts" width="267" height="150" viewBox="0 0 267 150" aria-label="Two donut charts and a bar chart">
      <g fill="none" stroke-width="3.6" transform="rotate(-90 47 89)">
        <circle cx="47" cy="89" r="17" stroke="var(--sky)" stroke-dasharray="56 107" stroke-dashoffset="-50"/>
        <circle cx="47" cy="89" r="17" stroke="var(--leaf)" stroke-dasharray="30 107" stroke-dashoffset="-20"/>
        <circle cx="47" cy="89" r="17" stroke="var(--sun)" stroke-dasharray="10 107" stroke-dashoffset="-10"/>
        <circle cx="47" cy="89" r="17" stroke="var(--deep-green)" stroke-dasharray="10 107"/>
      </g>
      <text class="chart-label" x="47" y="90.5" text-anchor="middle">Pie 01</text>
      <g fill="none" stroke-width="3.6" transform="rotate(-90 103 89)">
        <circle cx="103" cy="89" r="17" stroke="var(--sky)" stroke-dasharray="64 107" stroke-dashoffset="-43"/>
        <circle cx="103" cy="89" r="17" stroke="var(--leaf)" stroke-dasharray="25 107" stroke-dashoffset="-18"/>
        <circle cx="103" cy="89" r="17" stroke="var(--sun)" stroke-dasharray="9 107" stroke-dashoffset="-9"/>
        <circle cx="103" cy="89" r="17" stroke="var(--deep-green)" stroke-dasharray="9 107"/>
      </g>
      <text class="chart-label" x="103" y="90.5" text-anchor="middle">Pie 02</text>

      <line x1="134" y1="110.5" x2="256" y2="110.5" stroke="#dcdcdc" stroke-width="0.4"/>
      <g>
        <rect x="141" y="64" width="4.6" height="46" fill="var(--sky)"/>
        <rect x="146.5" y="84" width="4.6" height="26" fill="var(--leaf)"/>
        <rect x="152" y="89" width="4.6" height="21" fill="var(--sun)"/>

        <rect x="171" y="83" width="4.6" height="27" fill="var(--sky)"/>
        <rect x="176.5" y="63" width="4.6" height="47" fill="var(--leaf)"/>
        <rect x="182" y="89" width="4.6" height="21" fill="var(--sun)"/>

        <rect x="201" y="73" width="4.6" height="37" fill="var(--sky)"/>
        <rect x="206.5" y="91" width="4.6" height="19" fill="var(--leaf)"/>
        <rect x="212" y="78" width="4.6" height="32" fill="var(--sun)"/>

        <rect x="231" y="62" width="4.6" height="48" fill="var(--sky)"/>
        <rect x="236.5" y="80" width="4.6" height="30" fill="var(--leaf)"/>
        <rect x="242" y="56" width="4.6" height="54" fill="var(--sun)"/>
      </g>
      <text class="chart-label" x="150" y="116" text-anchor="middle">Category 1</text>
      <text class="chart-label" x="180" y="116" text-anchor="middle">Category 2</text>
      <text class="chart-label" x="210" y="116" text-anchor="middle">Category 3</text>
      <text class="chart-label" x="240" y="116" text-anchor="middle">Category 4</text>
      <g>
        <rect x="178" y="121.2" width="1" height="1" fill="var(--sky)"/>
        <text class="legend-label" x="179.6" y="122.2">Series 1</text>
        <rect x="189.5" y="121.2" width="1" height="1" fill="var(--leaf)"/>
        <text class="legend-label" x="191.1" y="122.2">Series 2</text>
        <rect x="201" y="121.2" width="1" height="1" fill="var(--sun)"/>
        <text class="legend-label" x="202.6" y="122.2">Series 3</text>
      </g>
    </svg>
    <div class="page-badge">17</div>
  </section>
</body>
</html>
```